Executive Business Card for Healthcare Company [Need Today]

I need a business card design for a healthcare company. The only branding the company has thus far is a logo. The cards will be utilized by company executives. The design I envision will be vibrant and appealing but with a corporate feel. They shouldn't be too casual or playful. I would like to complete this project TODAY if possible.

Target Market(s)

Healthcare vendors, other executives in healthcare and pharmaceuticals

Industry/Entity Type

Pharmaceutical

Contact Information for Business Card

See attachment

Font styles to use
Serif
Sans Serif

Colors

Designer to choose colors to be used in the design.

```html
<!DOCTYPE html>
<html lang="en">
<head>
<meta charset="utf-8">
<title>Corvane Health – Business Card</title>
<link href="https://fonts.googleapis.com/css2?family=Raleway:wght@300;400;500&display=swap" rel="stylesheet">
<style>
  :root {
    --bg: #e9eaec;
    --teal: #24b0c4;
    --green: #52b78d;
    --ink: #4a4d52;
    --muted: #6b6f74;
    --paper: #f7f7f7;
    --white: #ffffff;
  }
  * { box-sizing: border-box; margin: 0; padding: 0; }
  html, body { width: 1200px; height: 726px; overflow: hidden; }
  body {
    background: var(--bg);
    font-family: "Raleway", sans-serif;
    position: relative;
  }
  .card {
    position: absolute;
    top: 208px;
    width: 540px;
    height: 310px;
    border-radius: 3px;
    overflow: hidden;
    box-shadow: 0 6px 18px rgba(0,0,0,0.12);
  }

  /* Front side */
  .card-front {
    left: 36px;
    background: linear-gradient(160deg, var(--teal) 0%, var(--green) 100%);
    color: var(--white);
  }
  .card-front .halo {
    position: absolute;
    left: 170px; top: 20px;
    width: 270px; height: 270px;
    border-radius: 50%;
    border: 16px solid rgba(255,255,255,0.1);
  }
  .card-front .brand {
    position: absolute;
    left: 0; right: 0; top: 92px;
    text-align: center;
    font-weight: 300;
    line-height: 1;
  }
  .card-front .brand-name { font-size: 64px; letter-spacing: 1px; display: block; }
  .card-front .brand-sub { font-size: 30px; letter-spacing: 2px; display: block; margin-top: 6px; }
  .card-front .site {
    position: absolute;
    left: 0; right: 0; bottom: 30px;
    text-align: center;
    font-size: 13px;
    letter-spacing: 4px;
    font-weight: 400;
  }

  /* Back side */
  .card-back {
    left: 624px;
    background: var(--paper);
    color: var(--ink);
  }
  .card-back .halo {
    position: absolute;
    right: 40px; top: -30px;
    width: 200px; height: 200px;
    border-radius: 50%;
    border: 12px solid rgba(0,0,0,0.04);
  }
  .card-back .brand {
    position: absolute;
    left: 36px; top: 78px;
    width: 210px;
    text-align: center;
    color: var(--teal);
    font-weight: 300;
  }
  .card-back .brand-dot {
    width: 62px; height: 62px;
    border-radius: 50%;
    border: 2px solid var(--teal);
    margin: 0 auto 14px;
  }
  .card-back .brand-name { font-size: 42px; line-height: 1; display: block; }
  .card-back .brand-sub { font-size: 22px; letter-spacing: 1px; display: block; margin-top: 4px; }

  .contact {
    position: absolute;
    left: 290px; top: 62px;
  }
  .contact .person { font-size: 21px; font-weight: 500; color: var(--teal); }
  .contact .role { font-size: 10px; color: var(--muted); margin-top: 2px; margin-bottom: 12px; }
  .contact .line {
    display: flex; align-items: center; gap: 7px;
    font-size: 12.5px; line-height: 18px; color: var(--ink);
  }
  .contact .line svg { width: 10px; height: 10px; fill: var(--teal); flex: none; }
  .contact .line .accent { color: var(--teal); }
  .contact .address { font-size: 12.5px; line-height: 18px; margin-top: 4px; }

  .site-band {
    position: absolute;
    right: 0; bottom: 0;
    width: 250px; height: 54px;
    background: linear-gradient(90deg, var(--teal), var(--green));
    color: var(--white);
    font-size: 13px;
    letter-spacing: 1px;
    display: flex; align-items: center; justify-content: center;
  }
</style>
</head>
<body>

<section class="card card-front">
  <div class="halo"></div>
  <div class="brand">
    <span class="brand-name">corvane</span>
    <span class="brand-sub">health</span>
  </div>
  <div class="site">www.corvanerx.com</div>
</section>

<section class="card card-back">
  <div class="halo"></div>
  <div class="brand">
    <div class="brand-dot"></div>
    <span class="brand-name">corvane</span>
    <span class="brand-sub">health</span>
  </div>

  <div class="contact">
    <div class="person">Daniel Moreau</div>
    <div class="role">Senior Director of Marketing</div>
    <div class="line">
      <svg viewBox="0 0 10 10"><path d="M2 0.5 L4 2.5 L3 4 Q4.5 6 6 7 L7.5 6 L9.5 8 L8 9.5 Q3 9 0.5 2 Z"/></svg>
      <span>555-014-2273</span>
    </div>
    <div class="line">
      <svg viewBox="0 0 10 10"><path d="M2.5 0 H7.5 V10 H2.5 Z M3.5 1 V8 H6.5 V1 Z"/></svg>
      <span>555-019-6640</span>
    </div>
    <div class="line">
      <svg viewBox="0 0 10 10"><path d="M0 2 H10 V8 H0 Z M1 3 V7 H9 V3 L5 5.5 Z"/></svg>
      <span>dmoreau@<span class="accent">corvanerx</span>.com</span>
    </div>
    <div class="address">18 Linden Avenue<br>Fairview, GA 30000</div>
  </div>

  <div class="site-band">www.corvanerx.com</div>
</section>

</body>
</html>
```